Harborline Auto LLC

Car Dealer Customer Service
Address: 2874 Cresthaven Road, Shelbyville, TN 37162
web: www.harborlineautoxq.net
email: harborlineautoxq@mailnest.example
Phone: (931) 555-0148
Phone: (629) 555-0173

```html
<!DOCTYPE html>
<html lang="en">
<head>
<meta charset="utf-8">
<title>Harborline Auto LLC – Business Card</title>
<link href="https://fonts.googleapis.com/css2?family=Poppins:wght@400;600;700&display=swap" rel="stylesheet">
<style>
  :root {
    --bg: #3a3a3a;
    --card-white: #ffffff;
    --card-dark: #161616;
    --brand-blue: #1f7bb3;
    --brand-orange: #ecb043;
    --text-grey: #555a60;
    --edge-blue: #2a8fd0;
  }
  * { box-sizing: border-box; margin: 0; padding: 0; }
  html, body {
    width: 1200px; height: 801px; overflow: hidden;
    background: var(--bg);
    font-family: "Poppins", Arial, sans-serif;
  }
  .stage {
    width: 1200px; height: 801px;
    display: flex; align-items: center; justify-content: center; gap: 40px;
  }
  .card {
    position: relative; width: 540px; height: 309px; overflow: hidden;
    box-shadow: 0 18px 40px rgba(0,0,0,0.45);
  }
  .card--front { background: var(--card-white); border-bottom: 4px solid var(--brand-blue); }
  .card--back { background: var(--card-dark); border-bottom: 3px solid var(--edge-blue); }

  .wave { position: absolute; inset: 0; width: 100%; height: 100%; }

  .brand {
    position: absolute; left: 24px; top: 132px;
    display: flex; align-items: center; gap: 8px;
  }
  .brand__dot {
    width: 22px; height: 22px; border-radius: 50%;
    background: var(--brand-orange); flex: none;
  }
  .brand__name {
    font-weight: 700; font-size: 19px; letter-spacing: 0.4px;
    color: var(--brand-blue); text-transform: uppercase; white-space: nowrap;
  }

  .divider {
    position: absolute; left: 256px; top: 34px;
    width: 1.5px; height: 112px; background: var(--brand-blue);
  }

  .contact {
    position: absolute; left: 270px; top: 24px;
    font-size: 11.5px; line-height: 17px; color: var(--text-grey);
    white-space: nowrap;
  }
  .contact__title {
    font-weight: 600; font-size: 13px; color: var(--brand-blue); margin-bottom: 3px;
  }
  .contact__row { display: flex; align-items: center; gap: 6px; }
  .contact__row svg { width: 10px; height: 10px; flex: none; }
  .contact__gap { height: 6px; }

  .website {
    position: absolute; right: 26px; bottom: 28px;
    font-size: 12px; font-weight: 600; color: #ffffff; letter-spacing: 0.3px;
  }

  .back-mark {
    position: absolute; inset: 0;
    display: flex; align-items: center; justify-content: center; gap: 12px;
  }
  .back-mark__dot {
    width: 34px; height: 34px; border-radius: 50%; background: var(--brand-blue);
  }
  .back-mark__name {
    font-weight: 700; font-size: 26px; letter-spacing: 0.5px;
    color: var(--brand-orange); text-transform: uppercase;
  }
</style>
</head>
<body>
<main class="stage">
  <section class="card card--front" aria-label="Business card front">
    <svg class="wave" viewBox="0 0 540 309" preserveAspectRatio="none" aria-hidden="true">
      <path d="M0,309 C150,305 260,285 335,240 C405,195 465,172 540,162 L540,309 Z" fill="var(--brand-blue)"/>
      <path d="M150,302 C240,294 295,268 335,234 C400,182 460,160 540,150" fill="none" stroke="var(--brand-orange)" stroke-width="6"/>
    </svg>

    <div class="brand">
      <span class="brand__dot"></span>
      <span class="brand__name">Harborline Auto</span>
    </div>

    <div class="divider"></div>

    <div class="contact">
      <p class="contact__title">Car Dealer Customer Service</p>
      <p>2874 Cresthaven Road</p>
      <p>Shelbyville, TN 37162</p>
      <div class="contact__gap"></div>
      <p class="contact__row">
        <svg viewBox="0 0 10 10"><path d="M2,0.5 L3.6,0.5 L4.2,3 L3,3.8 C3.6,5.2 4.8,6.4 6.2,7 L7,5.8 L9.5,6.4 L9.5,8 C9.5,9 8.8,9.5 8,9.5 C4,9.2 0.8,6 0.5,2 C0.5,1.2 1,0.5 2,0.5 Z" fill="var(--brand-orange)"/></svg>
        (931) 555-0148
      </p>
      <p class="contact__row">
        <svg viewBox="0 0 10 10"><path d="M2,0.5 L3.6,0.5 L4.2,3 L3,3.8 C3.6,5.2 4.8,6.4 6.2,7 L7,5.8 L9.5,6.4 L9.5,8 C9.5,9 8.8,9.5 8,9.5 C4,9.2 0.8,6 0.5,2 C0.5,1.2 1,0.5 2,0.5 Z" fill="var(--brand-orange)"/></svg>
        (629) 555-0173
      </p>
      <p class="contact__row">
        <svg viewBox="0 0 10 10"><rect x="0.5" y="2" width="9" height="6.5" rx="0.8" fill="var(--brand-orange)"/><path d="M0.8,2.4 L5,5.6 L9.2,2.4" fill="none" stroke="#ffffff" stroke-width="0.9"/></svg>
        harborlineautoxq@mailnest.example
      </p>
    </div>

    <p class="website">www.harborlineautoxq.net</p>
  </section>

  <section class="card card--back" aria-label="Business card back">
    <div class="back-mark">
      <span class="back-mark__dot"></span>
      <span class="back-mark__name">Harborline Auto</span>
    </div>
  </section>
</main>
</body>
</html>
```